University Student Business Card

Looking for a professional university student business card. Student is studying business with a focus on marketing. Some combination using a monogram and/or full name on the front with full name, university details and contact information on the back. Card should be modern design for a young professional. Prefer use of royal blue, black and white but am open to other uses of colour palette if it reinforces young/trendy style. Initials for a monogram are: KR. Full details will be provided in private consultation with designer(s).

Target Market(s)

Professional business people, marketers, advertisers, consultants

Industry/Entity Type

Business, marketing

Contact Information for Business Card

Monogram or personal logo, full name, university name, program of study, phone number, email address, pathfolio address

Other font styles liked:
• Open to suggestion to fulfill above requirements

Colors
0054AA
0677BA
7BADD7
CADEEF
E8F1F8

Requirements
Must have
• Monogram using letters K and R, and incorporate the business card details listed in the brief (specific details including personal contact info will be shared with successful designer to ensure privacy)
Nice to have
• Personal brand using monogram or personal logo (not a business logo)

```html
<!DOCTYPE html>
<html lang="en">
<head>
<meta charset="UTF-8">
<title>Daniel Hayes — Student Business Card</title>
<link rel="stylesheet" href="https://fonts.googleapis.com/css2?family=Montserrat:wght@500;600;700&family=Arimo:wght@400&display=swap">
<style>
  :root {
    --royal: #0054AA;
    --royal-soft: #1461AE;
    --accent: #0677BA;
    --ink: #1c1c1c;
    --paper: #ffffff;
    --backdrop: #c9c9c9;
    --rule-light: #d6d6d6;
    --rule-dark: rgba(255,255,255,0.35);
  }
  * { box-sizing: border-box; margin: 0; padding: 0; }
  html, body { width: 1200px; height: 900px; overflow: hidden; }
  body { background: var(--backdrop); position: relative; font-family: "Arimo", Arial, sans-serif; }

  .card {
    position: absolute;
    width: 640px;
    height: 366px;
    border-radius: 40px;
    overflow: hidden;
    box-shadow: 0 6px 14px rgba(0,0,0,0.25);
  }
  .card--front { left: 110px; top: 50px; background: var(--paper); }
  .card--back { left: 450px; top: 484px; background: var(--royal); }

  /* Front */
  .front-content {
    position: absolute; inset: 0;
    display: flex; flex-direction: column; align-items: center; justify-content: center;
    text-align: center;
  }
  .monogram {
    font-family: "Montserrat", sans-serif;
    font-weight: 700;
    font-size: 110px;
    line-height: 1;
    letter-spacing: 4px;
    color: var(--royal);
  }
  .holder-name {
    margin-top: 18px;
    font-family: "Montserrat", sans-serif;
    font-weight: 600;
    font-size: 24px;
    letter-spacing: 1px;
    color: var(--royal);
  }
  .program {
    margin-top: 2px;
    font-size: 15px;
    letter-spacing: 0.5px;
    color: var(--ink);
  }
  .front-rule { width: 120px; height: 1px; background: var(--rule-light); margin: 14px 0 12px; }
  .profile-link { display: flex; align-items: center; gap: 8px; font-size: 15px; color: var(--ink); letter-spacing: 0.3px; }
  .profile-dot { width: 22px; height: 22px; border-radius: 50%; background: var(--accent); }

  /* Back */
  .back-watermark {
    position: absolute;
    left: 50%; top: 50%;
    transform: translate(-50%, -52%);
    font-family: "Montserrat", sans-serif;
    font-weight: 700;
    font-size: 300px;
    line-height: 1;
    letter-spacing: 10px;
    color: var(--royal-soft);
  }
  .back-content {
    position: absolute; inset: 0;
    display: flex; flex-direction: column; align-items: center; justify-content: center;
    text-align: center;
    color: var(--paper);
  }
  .university {
    font-family: "Montserrat", sans-serif;
    font-weight: 600;
    font-size: 27px;
    letter-spacing: 1.5px;
  }
  .back-rule { width: 110px; height: 1px; background: var(--rule-dark); margin: 12px 0; }
  .details { font-size: 15px; line-height: 1.3; letter-spacing: 0.4px; }
</style>
</head>
<body>
  <section class="card card--front" aria-label="Card front">
    <div class="front-content">
      <div class="monogram">KR</div>
      <div class="holder-name">DANIEL HAYES</div>
      <div class="program">Business Marketing</div>
      <div class="front-rule"></div>
      <div class="profile-link"><span class="profile-dot"></span><span>pathfolio.com/name</span></div>
    </div>
  </section>

  <section class="card card--back" aria-label="Card back">
    <div class="back-watermark" aria-hidden="true">KR</div>
    <div class="back-content">
      <div class="university">UNIVERSITY NAME</div>
      <div class="back-rule"></div>
      <div class="details">
        <p>87, Maple Court Avenue</p>
        <p>31208, Northland</p>
      </div>
      <div class="back-rule"></div>
      <div class="details">
        <p>071-555 018 273</p>
        <p>hello@krmail.com</p>
        <p>www.krportfolio.com</p>
      </div>
    </div>
  </section>
</body>
</html>
```